HearthMile business card and stationary design

We are looking for a simple yet elegant design for our mortgage company business card and stationary.

The card should include:
Name (Marcus Pell)
Title (CEO)
Phone Number (732-555-0182)
Address (48 Birchwell Court, Suite 314, Hazlet, NJ 07730)
Email (email@hearthmile.example)
"NMLS" i.e. (NMLS 61947)
"Company NMLS" (Company NMLS 274615)

Contact Information for Business Card

See above

```html
<!DOCTYPE html>
<html lang="en">
<head>
<meta charset="utf-8">
<title>HearthMile Business Card</title>
<link href="https://fonts.googleapis.com/css2?family=Montserrat:wght@500;700&family=Arimo:wght@400&display=swap" rel="stylesheet">
<style>
  :root {
    --backdrop: #a9a9a9;
    --navy: #182531;
    --brand-blue: #00a8e8;
    --ink: #1e1e1e;
    --paper: #ffffff;
    --rule: #8a8a8a;
  }
  html, body {
    margin: 0;
    padding: 0;
    width: 1200px;
    height: 1200px;
    overflow: hidden;
    background: var(--backdrop);
  }
  .stage {
    position: relative;
    width: 1200px;
    height: 1200px;
  }
  .card {
    position: absolute;
    top: 303px;
    width: 368px;
    height: 594px;
    box-shadow: 3px 4px 6px rgba(0,0,0,0.35);
    font-family: "Arimo", Arial, sans-serif;
    text-align: center;
  }
  .card--back {
    left: 201px;
    background: var(--navy);
  }
  .card--front {
    left: 599px;
    width: 364px;
    background: var(--paper);
  }
  .wordmark {
    position: absolute;
    left: 0;
    right: 0;
    font-family: "Montserrat", Arial, sans-serif;
    font-weight: 500;
    font-size: 45px;
    letter-spacing: 0.5px;
    line-height: 1;
  }
  .card--back .wordmark { top: 288px; color: var(--paper); }
  .card--front .wordmark { top: 174px; color: var(--navy); }

  .licences {
    position: absolute;
    left: 0;
    right: 0;
    top: 512px;
    font-size: 17px;
    line-height: 22px;
    color: var(--paper);
  }
  .accent { color: var(--brand-blue); }

  .person {
    position: absolute;
    left: 0;
    right: 0;
    top: 336px;
  }
  .person__name {
    font-family: "Montserrat", Arial, sans-serif;
    font-weight: 700;
    font-size: 25px;
    line-height: 28px;
    color: var(--ink);
  }
  .person__title {
    font-size: 17px;
    line-height: 20px;
    color: var(--ink);
  }
  .icon-row {
    position: absolute;
    top: 396px;
    left: 87px;
    width: 190px;
    height: 25px;
    display: flex;
    align-items: center;
    justify-content: space-between;
  }
  .icon-row__line {
    width: 51px;
    height: 1px;
    background: var(--rule);
  }
  .icon-row__icons { display: flex; gap: 4px; }
  .icon-tile {
    width: 25px;
    height: 25px;
    border-radius: 3px;
    background: var(--brand-blue);
    display: flex;
    align-items: center;
    justify-content: center;
  }
  .contact {
    position: absolute;
    left: 0;
    right: 0;
    top: 431px;
    font-size: 16px;
    line-height: 22px;
    color: var(--ink);
  }
  .divider {
    position: absolute;
    top: 507px;
    left: 88px;
    width: 195px;
    height: 1px;
    background: var(--rule);
  }
  .address {
    position: absolute;
    left: 0;
    right: 0;
    top: 520px;
    font-size: 17px;
    line-height: 22px;
    color: var(--ink);
  }
</style>
</head>
<body>
<div class="stage">
  <section class="card card--back">
    <div class="wordmark">HearthMile</div>
    <div class="licences">
      <div><span class="accent">NMLS</span> 61947</div>
      <div><span class="accent">Company NMLS</span> 274615</div>
    </div>
  </section>

  <section class="card card--front">
    <div class="wordmark">HearthMile</div>
    <div class="person">
      <div class="person__name">Marcus <span class="accent">Pell</span></div>
      <div class="person__title">CEO</div>
    </div>
    <div class="icon-row">
      <span class="icon-row__line"></span>
      <div class="icon-row__icons">
        <span class="icon-tile">
          <svg width="15" height="15" viewBox="0 0 16 16" aria-label="Phone">
            <path d="M2 6 Q8 1 14 6 L12 8 L10 6.5 L10 5 Q8 4.3 6 5 L6 6.5 L4 8 Z" fill="#fff"/>
            <rect x="4" y="8" width="8" height="5" rx="1" fill="#fff"/>
          </svg>
        </span>
        <span class="icon-tile">
          <svg width="16" height="13" viewBox="0 0 16 12" aria-label="Email">
            <rect x="1" y="1" width="14" height="10" fill="none" stroke="#fff" stroke-width="1.3"/>
            <path d="M1 1 L8 7 L15 1 M1 11 L6 5.5 M15 11 L10 5.5" fill="none" stroke="#fff" stroke-width="1.1"/>
          </svg>
        </span>
        <span class="icon-tile">
          <svg width="16" height="16" viewBox="0 0 16 16" aria-label="Website">
            <circle cx="8" cy="8" r="6.5" fill="none" stroke="#fff" stroke-width="1.3"/>
            <ellipse cx="8" cy="8" rx="2.8" ry="6.5" fill="none" stroke="#fff" stroke-width="1"/>
            <path d="M1.5 8 H14.5" stroke="#fff" stroke-width="1"/>
          </svg>
        </span>
      </div>
      <span class="icon-row__line"></span>
    </div>
    <div class="contact">
      <div>732-555-0182</div>
      <div>email@hearthmile.example</div>
      <div>www.<span class="accent">hearthmile</span>.example</div>
    </div>
    <div class="divider"></div>
    <div class="address">
      <div>48 Birchwell Court, Suite 314</div>
      <div>Larkmoor, NJ 07799</div>
    </div>
  </section>
</div>
</body>
</html>
```